Specialised investor in e-mobility and energy wants business card design

We need a business card design that fits our existing corporate design. <The look and feel must be 'sharp'/'clean', dynamic, communicate momentum, professionalism etc (as one would imagine from a firm in the financial sector). We like the idea of a reverse-side of the card that includes the logo, and the name and contact details on the other. We expect the deliverable to be whatever format might be required to be able to get cards printed directly by a service such as kelmo press. Our website is www.zub.capital

```html
<!DOCTYPE html>
<html lang="en">
<head>
<meta charset="utf-8">
<title>ZUB Capital – Business Card</title>
<link href="https://fonts.googleapis.com/css2?family=EB+Garamond:wght@400;600&family=Questrial&display=swap" rel="stylesheet">
<style>
  :root {
    --bg: #e9eae7;
    --green-dark: #3c6526;
    --green-mid: #4f7d32;
    --green-light: #74a342;
    --accent-line: #9cc36a;
    --white: #ffffff;
    --paper: #f6f6f4;
    --ink: #4a4a4a;
    --name: #2f5a1e;
  }
  * { box-sizing: border-box; margin: 0; padding: 0; }
  html, body { width: 1200px; height: 900px; overflow: hidden; }
  body { background: var(--bg); position: relative; font-family: "EB Garamond", Georgia, serif; }

  .card {
    position: absolute;
    left: 250px;
    width: 700px;
    height: 400px;
    border-radius: 0 46px 0 46px;
    box-shadow: 0 10px 24px rgba(0,0,0,.18);
    overflow: hidden;
  }

  /* Front: brand side */
  .card--front {
    top: 35px;
    background: radial-gradient(ellipse at 45% 70%, var(--green-light) 0%, var(--green-mid) 45%, var(--green-dark) 100%);
  }
  .brand {
    position: absolute;
    display: flex;
    align-items: center;
    gap: 14px;
    font-family: "Questrial", "Century Gothic", sans-serif;
    font-weight: 400;
    white-space: nowrap;
  }
  .card--front .brand { left: 120px; top: 250px; font-size: 64px; color: var(--white); }
  .brand__mark { width: 22px; height: 22px; background: currentColor; display: inline-block; }

  /* Back: contact side */
  .card--back {
    top: 465px;
    background: linear-gradient(160deg, var(--white) 0%, var(--paper) 100%);
    color: var(--ink);
  }
  .person { position: absolute; left: 58px; top: 52px; }
  .person__name { font-size: 26px; font-weight: 600; letter-spacing: .5px; color: var(--name); text-transform: uppercase; }
  .person__role { font-size: 20px; margin-top: -2px; }

  .contact { position: absolute; left: 92px; top: 150px; list-style: none; font-size: 22px; line-height: 32px; }
  .contact li { display: flex; align-items: center; gap: 12px; }
  .contact svg { width: 18px; height: 18px; fill: none; stroke: var(--ink); stroke-width: 1.6; }

  .divider { position: absolute; left: 0; top: 300px; width: 470px; height: 1.5px; background: var(--accent-line); }

  .card--back .brand { left: 70px; top: 312px; font-size: 60px; color: var(--name); }

  .office { position: absolute; right: 54px; top: 150px; text-align: right; font-size: 22px; line-height: 28px; }
</style>
</head>
<body>

<section class="card card--front" aria-label="Card front">
  <div class="brand"><span class="brand__mark"></span>ZUB Capital</div>
</section>

<section class="card card--back" aria-label="Card back">
  <div class="person">
    <p class="person__name">Paul Harrowe</p>
    <p class="person__role">Partner</p>
  </div>

  <ul class="contact">
    <li>
      <svg viewBox="0 0 18 18"><rect x="5" y="1.5" width="8" height="15" rx="1.5"/><line x1="8" y1="14" x2="10" y2="14"/></svg>
      +41 79555 0148
    </li>
    <li>
      <svg viewBox="0 0 18 18"><rect x="2" y="4" width="14" height="10" rx="1"/><polyline points="2,4 9,10 16,4"/></svg>
      paul@zub.capital
    </li>
    <li>
      <svg viewBox="0 0 18 18"><circle cx="9" cy="9" r="7"/><ellipse cx="9" cy="9" rx="3" ry="7"/><line x1="2" y1="9" x2="16" y2="9"/></svg>
      www.zub.capital
    </li>
  </ul>

  <div class="office">
    <p>ZUB Capital S.A.</p>
    <p>Geneva, Switzerland</p>
  </div>

  <div class="divider"></div>

  <div class="brand"><span class="brand__mark"></span>ZUB Capital</div>
</section>

</body>
</html>
```